Web Design Project

Due to client commitments, we don't have time in-house to complete this project...
We need a design refresh for our web company! It's time for us to move things along, so we're looking to SketchBazaar to get this done!
Our clients tend to be associations and government, with some element of business clients. We need a design that appeals to this sophisticated target market.
Our current web site can be found at www.tallowbrookweb.ca. We are looking for a more personable, contemporary look for the new site design. However, you can see our logo on this site, and some of the content.
The design you provide will be implemented in Quillmark. The design winner will only need to provide the PSD or Fireworks PNG format. We anticipate creating the template coding in-house.
However, if you have experience creating Quillmark templates, please let us know as we may ask you to bid separately to do that phase of the project.
We've provided you with wireframes of the home page and the inside page, along with Adobe Illustrator and PSD versions of our logo.
For the home page, we've indicated that we'd like to have a slider implemented into the design. For the purpose of design, we believe we'll use this slider: http://demo.vorntiplugins.com/zesty-panelle-slider.html.
The slider will contain inspiration photos related to each of the tabs. Ideally, we would like you to suggest the images for the slider. The dimension of the slider can be adjusted. We would like more space for the image with less for the text. The slider height should be sufficient to ensure the image "stimulates" the audience and sets the tone for the landing page.
The wireframe is provided to illustrate the placement of content and menu items. The exact dimensions of each component can be revised as you see fit.
Target Market(s)
Our clients tend to be associations, non-profit, government, and business clients. We need a design that appeals to this sophisticated target market.
Industry/Entity Type
Business
Look and feel

```html
<!DOCTYPE html>
<html lang="en">
<head>
<meta charset="utf-8">
<title>Tallowbrook Web – Home</title>
<link href="https://fonts.googleapis.com/css2?family=Arimo:wght@400;700&display=swap" rel="stylesheet">
<style>
:root{
  --page:#ecebea;
  --topbar:#7c0f0c;
  --topbar-pill:#5a0806;
  --accent-red:#d8321d;
  --nav:#353535;
  --nav-line:#555;
  --panel:#ffffff;
  --well:#e6e6ea;
  --card-edge:#c9c9cf;
  --ink:#222;
  --muted:#555;
  --orange:#f39a1e;
  --footer-bar:#3a3a3a;
}
*{box-sizing:border-box;margin:0;padding:0}
html,body{width:1057px;height:1200px;overflow:hidden}
body{background:var(--page);font-family:"Arimo",Arial,sans-serif;color:var(--ink);position:relative;font-size:11px}
.abs{position:absolute}
.topbar{left:0;top:0;width:1057px;height:28px;background:var(--topbar);color:#fff;font-size:10px}
.topbar .pill{top:6px;height:18px;line-height:18px;padding:0 12px}
.topbar .pill.dark{background:var(--topbar-pill)}
.topbar .contact{right:88px;top:9px;color:#f4c9c0}
.topbar .contact b{color:#ff8a70}
.brand{left:87px;top:45px;display:flex;align-items:center;gap:10px}
.brand .mark{width:62px;height:62px;border-radius:50%;background:var(--accent-red)}
.brand .name{font-size:24px;font-weight:700;color:#2b2b2b}
.quote{left:828px;top:56px;width:141px;height:25px;background:var(--orange);border-radius:2px;color:#fff;font-size:14px;text-align:center;line-height:25px}
.social{top:93px;width:18px;height:18px;border-radius:3px;background:#6f8fb8}
.nav{left:87px;top:123px;width:881px;height:37px;background:var(--nav);display:flex}
.nav a{color:#fff;text-decoration:none;font-size:12px;line-height:37px;text-align:center;border-right:1px solid var(--nav-line)}
.nav a.current{color:var(--accent-red)}
.main{left:87px;top:175px;width:881px;height:850px;background:var(--panel)}
.tabs{left:109px;top:177px;display:flex;font-size:11px}
.tabs span{padding:0 15px;height:25px;line-height:25px;border-right:1px solid #ddd}
.tabs span.on{background:var(--well)}
.slider{left:101px;top:202px;width:852px;height:376px;background:var(--well)}
.slide{left:109px;top:209px;width:837px;height:361px;background:linear-gradient(90deg,#c99a78 0%,#eee9e4 28%,#f4f4f2 50%,#eee9e4 72%,#c99a78 100%)}
.service{top:597px;width:151px;height:121px;background:var(--well);border-bottom:2px solid var(--card-edge)}
.service .thumb{position:absolute;left:6px;top:5px;width:139px;height:95px;background:#fff}
.service .thumb i{position:absolute;left:40px;top:12px;width:60px;height:60px;border-radius:8px}
.service .title{position:absolute;left:0;right:0;top:87px;text-align:center;font-size:11px}
.service .sub{position:absolute;left:0;right:0;top:101px;text-align:center;font-size:10px}
.lower{left:101px;top:739px;width:851px;height:273px;background:var(--well)}
.lower .divider{left:470px;top:0;width:1px;height:273px;background:#999}
.head{background:#fff;height:28px;line-height:28px;padding-left:10px;font-size:17px}
.blog-head{left:9px;top:9px;width:433px}
.blog-art{left:20px;top:50px;width:153px;height:120px;background:radial-gradient(#d63a2a,#e9c9c4 70%,var(--well))}
.blog-text{left:25px;top:44px;width:415px;font-size:11px;line-height:17px;color:#333}
.blog-text .float{float:left;width:162px;height:145px}
.proj-head{left:499px;top:9px;width:341px}
.proj{left:502px;width:340px;height:60px;font-size:11px;line-height:13.5px;color:#333}
.proj .shot{position:absolute;left:0;top:0;width:88px;height:56px}
.proj p{position:absolute;left:108px;top:0}
.proj-rule{left:502px;width:337px;border-top:1px dashed #999}
.fcol{top:1046px;font-size:10px;line-height:15.3px}
.fcol h4{font-size:11px;margin-bottom:4px}
.fsep{top:1063px;width:1px;height:76px;background:#bbb}
.footbar{left:87px;top:1167px;width:881px;height:33px;background:var(--footer-bar);color:#ddd;font-size:10px}
.footbar .links{left:13px;top:11px}
.footbar .copy{right:16px;top:13px;font-size:9px}
</style>
</head>
<body>
<header>
  <div class="abs topbar">
    <span class="abs pill dark" style="left:87px">www.MapleNestSurveys.ca</span>
    <span class="abs pill" style="left:276px">www.RideauSiteCraft.ca</span>
    <span class="abs contact"><b>Contact us today : 613 555 0142</b> &nbsp;|&nbsp; sales@tallowbrookweb.ca</span>
  </div>
  <div class="abs brand"><span class="mark"></span><span class="name">Tallowbrook Web</span></div>
  <div class="abs quote">Request a Quote</div>
  <span class="abs social" style="left:921px" aria-label="Social link"></span>
  <span class="abs social" style="left:950px" aria-label="Social link"></span>
  <nav class="abs nav">
    <a class="current" style="width:84px">Home</a>
    <a style="width:114px">Web Design</a>
    <a style="width:113px">Mobile Apps</a>
    <a style="width:141px">Custom Software</a>
    <a style="width:166px">Accessibile PDF/HTML</a>
    <a style="width:160px">CMC: Quillmark/Nodeway</a>
    <a style="width:103px;border-right:0">Contact us</a>
  </nav>
</header>

<main>
  <div class="abs main"></div>
  <div class="abs tabs"><span class="on">Our Vision</span><span>Business</span><span>Government</span><span style="border:0">Associations / Non-Profit</span></div>
  <div class="abs slider"></div>
  <div class="abs slide" role="img" aria-label="Photo of two cupped hands around a young seedling growing in a mound of soil"></div>

  <div class="abs service" style="left:101px"><div class="thumb" role="img" aria-label="Colourful puzzle pieces"><i style="background:linear-gradient(135deg,#3a9be0,#e24a7a,#f2c21c)"></i></div><div class="title">Web Design</div><div class="sub">Lorem Ipsem Lorem Ipsem</div></div>
  <div class="abs service" style="left:277px"><div class="thumb" role="img" aria-label="Cube covered in app tiles"><i style="background:linear-gradient(135deg,#333,#5a6f8e)"></i></div><div class="title">Mobile Apps</div><div class="sub">Lorem Ipsem Lorem Ipsem</div></div>
  <div class="abs service" style="left:452px"><div class="thumb" role="img" aria-label="Stack of pale blue blocks"><i style="background:linear-gradient(135deg,#cfe2ef,#8fb3cc)"></i></div><div class="title">Custom Software</div><div class="sub">Lorem Ipsem Lorem Ipsem</div></div>
  <div class="abs service" style="left:627px"><div class="thumb" role="img" aria-label="Document with a globe"><i style="background:linear-gradient(135deg,#9fd66a,#3f8f4a)"></i></div><div class="title">Accessible PDF / HTML</div><div class="sub">Lorem Ipsem Lorem Ipsem</div></div>
  <div class="abs service" style="left:802px"><div class="thumb" role="img" aria-label="Content system icon on a white tile"><i style="background:linear-gradient(135deg,#f1f1f1,#d6d6d6)"></i></div><div class="title">CMS; Quillmark / Nodeway</div><div class="sub">Lorem Ipsem Lorem Ipsem</div></div>

  <section class="abs lower">
    <div class="abs divider"></div>
    <h2 class="abs head blog-head" style="font-weight:400">Blog</h2>
    <div class="abs blog-art" role="img" aria-label="Red word cloud of the word blog"></div>
    <p class="abs blog-text"><span class="float"></span>Lorem Ipsum is simply dummy text of the printing and typesetting industry. Lorem Ipsum has been the industry's standard dummy text ever since the 1500s, when an unknown printer took a galley of type and scrambled it to make a type specimen book. It has survived not only five centuries, but also the leap into electronic typesetting, remaining essentially unchanged. It was popularised in the 1960s with the release of Typeframe sheets containing Lorem Ipsum passages, and more recently with desktop publishing software like Folio LayoutDesk including versions of Lorem Ipsum. It was popularised in the 1960s with the release of Typeframe sheets containing versions of Lorem Ipsum.</p>

    <h2 class="abs head proj-head" style="font-weight:400">Featured Projects</h2>
    <div class="abs proj" style="top:50px"><div class="shot" role="img" aria-label="Website screenshot with a landscape header" style="background:linear-gradient(#2d5f86,#dfe6e8)"></div><p>Project description summary #1<br>could be up to<br>Five<br>Lines of text</p></div>
    <div class="abs proj-rule" style="top:115px"></div>
    <div class="abs proj" style="top:126px"><div class="shot" role="img" aria-label="Phone surrounded by app icons" style="background:linear-gradient(135deg,#e8f0f6,#4a7fc0,#e8f0f6)"></div><p>Project description summary #2<br>could be up to<br>Five<br>Lines of text</p></div>
    <div class="abs proj-rule" style="top:193px"></div>
    <div class="abs proj" style="top:204px"><div class="shot" role="img" aria-label="Pile of design magazines" style="background:linear-gradient(135deg,#2a2a2a,#c8622e,#e7b530)"></div><p>Project description summary #3<br>could be up to<br>Five<br>Lines of text</p></div>
  </section>
</main>

<footer>
  <div class="abs fcol" style="left:101px"><h4>Web Design</h4>Item One<br>Item Two<br>Item Three<br>Item Four<br>Item Five</div>
  <div class="abs fsep" style="left:264px"></div>
  <div class="abs fcol" style="left:355px"><h4>Mobile Apps</h4>Item One<br>Item Two<br>Item Three<br>Item Four<br>Item Five</div>
  <div class="abs fsep" style="left:502px"></div>
  <div class="abs fcol" style="left:582px"><h4>Accessible PDF / HTML</h4>Item One<br>Item Two<br>Item Three<br>Item Four<br>Item Five</div>
  <div class="abs fsep" style="left:768px"></div>
  <div class="abs fcol" style="left:840px"><h4>CMS: Quillmark / Nodeway</h4>Item One<br>Item Two<br>Item Three<br>Item Four<br>Item Five</div>
  <div class="abs footbar">
    <span class="abs links">Home | Web Design | Mobile Apps | Custom Software | Accessibile PDF/HTML | CMC: Quillmark/Nodeway | Contact us</span>
    <span class="abs copy">© Tallowbrook Web 2011</span>
  </div>
</footer>
</body>
</html>
```